Orbit Voltix VR is the name of our project, We are a Virtual Reality Theme park

We need a web page and logo that is sharp and exciting, and futuristic that people would want to have on a tee shirt.. We like teal -black- silver colour. Customers will be able to book on line- we will have Free Roam VR experiences , Trundla(treadmills), Stand alone VR stations and VR Simulator rides.

Orbit Voltix VR

```html
<!DOCTYPE html>
<html lang="en">
<head>
<meta charset="utf-8">
<title>Orbit Voltix VR</title>
<link rel="stylesheet" href="https://fonts.googleapis.com/css2?family=Lora:wght@400&family=Titillium+Web:wght@400;600&family=Open+Sans:wght@400;600&display=swap">
<style>
  :root {
    --teal: #1f9690;
    --teal-dark: #17807b;
    --blue: #5b79d6;
    --hero-grey: #565656;
    --ink: #333333;
    --muted: #666666;
    --soft-bg: #f4f4f4;
    --white: #ffffff;
    --footer: #2b2b2b;
  }
  * { margin: 0; padding: 0; box-sizing: border-box; }
  html, body { width: 1200px; height: 3125px; overflow: hidden; }
  body { position: relative; background: var(--white); font-family: "Open Sans", Arial, sans-serif; color: var(--ink); }
  .abs { position: absolute; }

  /* Hero */
  .hero { left: 0; top: 0; width: 1200px; height: 652px;
    background: linear-gradient(100deg, #5a5a5a 0%, #545454 60%, #5c6a9a 88%, #5f7fd8 100%); overflow: hidden; }
  .hero-visual { right: 0; top: 125px; width: 492px; height: 527px;
    background: radial-gradient(ellipse at 55% 40%, #e8e8ea 0%, #bdbfc4 40%, rgba(120,124,140,0.4) 70%, rgba(90,90,90,0) 85%); }
  .brand { left: 112px; top: 34px; font-family: "Lora", Georgia, serif; font-size: 34px; color: var(--white); }
  .main-nav { left: 614px; top: 50px; display: flex; gap: 0; font-size: 13px; font-weight: 600; color: var(--white); }
  .main-nav span { position: absolute; white-space: nowrap; }
  .main-nav .active { color: var(--teal); }
  .hero-title { left: 112px; top: 254px; font-family: "Titillium Web", sans-serif; font-weight: 600; font-size: 46px; color: var(--white); letter-spacing: 0.5px; }
  .hero-text { left: 112px; top: 336px; width: 560px; font-family: "Titillium Web", sans-serif; font-weight: 600; font-size: 19px; line-height: 38px; color: var(--white); }
  .btn { display: flex; align-items: center; justify-content: center; background: var(--teal); color: var(--white); }
  .hero-btn { left: 112px; top: 433px; width: 136px; height: 50px; font-family: "Titillium Web", sans-serif; font-weight: 600; font-size: 19px; }

  /* Welcome */
  .welcome { left: 0; top: 652px; width: 1200px; height: 633px; background: var(--soft-bg); }
  .welcome-photo { left: 598px; top: 710px; width: 456px; height: 511px;
    background: linear-gradient(150deg, #2a3040 0%, #3a5aa0 45%, #1f4fa8 75%, #2d3f78 100%); }
  .welcome-card { left: 112px; top: 765px; width: 546px; height: 406px; background: var(--white); box-shadow: 0 2px 8px rgba(0,0,0,0.06); }
  .welcome-kicker { left: 158px; top: 802px; font-family: "Titillium Web", sans-serif; font-size: 23px; color: var(--muted); }
  .welcome-title { left: 158px; top: 833px; font-family: "Titillium Web", sans-serif; font-size: 40px; color: var(--teal); }
  .welcome-text { left: 158px; top: 902px; width: 440px; font-family: Arial, sans-serif; font-size: 11.5px; line-height: 26px; color: var(--muted); }
  .welcome-btn { left: 158px; top: 1090px; width: 136px; height: 50px; font-family: "Open Sans", sans-serif; font-size: 14px; font-weight: 600; }

  /* Featured */
  .featured-block { left: 112px; top: 1352px; width: 407px; height: 308px; background: linear-gradient(160deg, var(--blue) 0%, #3a8fa8 60%, var(--teal) 100%); }
  .featured-photo { left: 148px; top: 1396px; width: 425px; height: 310px;
    background: linear-gradient(135deg, #1c2c48 0%, #2c5e8a 45%, #6a8fb0 65%, #1e2d44 100%); }
  .section-title { font-family: "Titillium Web", sans-serif; font-size: 40px; color: var(--teal); }
  .featured-title { left: 631px; top: 1344px; }
  .featured-text { left: 636px; top: 1412px; width: 430px; font-size: 12.5px; line-height: 25px; color: var(--muted); }
  .feature-list { left: 636px; top: 1512px; list-style: none; }
  .feature-list li { position: relative; height: 40px; padding-left: 44px; font-size: 12.5px; line-height: 26px; color: var(--muted); }
  .feature-list svg { position: absolute; left: 0; top: 7px; }

  /* Video */
  .video-band { left: 587px; top: 1792px; width: 613px; height: 510px; background: linear-gradient(135deg, var(--teal) 0%, #1f9690 55%, var(--blue) 100%); }
  .video-frame { left: 112px; top: 1835px; width: 905px; height: 425px;
    background: radial-gradient(ellipse at 55% 35%, #3a3d8c 0%, #1c2f9e 45%, #14205e 100%); }
  .play { left: 523px; top: 2006px; }

  /* Services */
  .services-title { left: 0; top: 2364px; width: 1200px; text-align: center; }
  .services-sub { left: 0; top: 2431px; width: 1200px; text-align: center; font-size: 13.5px; color: var(--ink); }
  .service { width: 236px; top: 2485px; height: 300px; }
  .service-photo { width: 236px; height: 233px; }
  .service-label { width: 236px; height: 67px; display: flex; align-items: center; justify-content: center;
    background: var(--teal); color: var(--white); font-family: "Titillium Web", sans-serif; font-weight: 600; font-size: 17px; }

  /* Footer */
  .footer { left: 0; top: 2858px; width: 1200px; height: 267px; background: var(--footer); }
  .footer-brand { left: 0; top: 2900px; width: 1200px; text-align: center; font-family: "Lora", Georgia, serif; font-size: 49px; color: var(--white); }
  .footer-nav { left: 0; top: 3002px; width: 1200px; display: flex; justify-content: center; gap: 28px; font-size: 13px; color: var(--white); }
  .copyright { left: 0; top: 3061px; width: 1200px; text-align: center; font-size: 13px; color: var(--white); }
</style>
</head>
<body>

<header class="abs hero">
  <div class="abs hero-visual" role="img" aria-label="Silver humanoid figure wearing a VR headset among connected network lines"></div>
</header>
<div class="abs brand">Orbit Voltix VR</div>
<nav class="abs main-nav">
  <span class="active" style="left:0">HOME</span>
  <span style="left:86px">ABOUT US</span>
  <span style="left:198px">SERVICES</span>
  <span style="left:309px">NEWS</span>
  <span style="left:394px">CONTACT US</span>
</nav>
<h1 class="abs hero-title">ORBIT VOLTIX VR</h1>
<p class="abs hero-text">Sed ut perspiciatis unde omnis iste natus error sit voluptatem accusantium doloremque laudantium</p>
<div class="abs btn hero-btn">Read More</div>

<section class="abs welcome"></section>
<div class="abs welcome-photo" role="img" aria-label="VR headset resting on a table with city lights behind"></div>
<div class="abs welcome-card"></div>
<div class="abs welcome-kicker">WELCOME TO</div>
<h2 class="abs welcome-title">ORBIT VOLTIX VR</h2>
<p class="abs welcome-text">Sed ut perspiciatis unde omnis iste natus error sit voluptatem accusantium dolore que laudantium, totam rem aperiam, eaque ipsa quae ab illo inventore veritatis et quasi architecto beatae vitae dicta sunt explicabo. Nemo enim ipsam voluptatem quia voluptas sit aspernatur aut odit aut fugit, sed quia consequuntur magni dolores eos qui ratione voluptatem sequi nesciunt.Neque porro quisquam est, qui dolorem ipsum quia dolor sit amet, consectetur, adipisci velit</p>
<div class="abs btn welcome-btn">READ MORE</div>

<div class="abs featured-block"></div>
<div class="abs featured-photo" role="img" aria-label="Player in a VR headset aiming a futuristic blaster with holographic rings"></div>
<h2 class="abs section-title featured-title">OUR FEATURED</h2>
<p class="abs featured-text">Sed ut perspiciatis unde omnis iste natus error sit voluptatem accusanti um dolorem que laudantium, totam rem aperiam, eaque ipsa quae ab illo quasi architecto beatae vitae dicta sunt explicabo.</p>
<ul class="abs feature-list">
  <li><svg width="14" height="12" viewBox="0 0 14 12"><path d="M1 6l4 4 8-9" fill="none" stroke="#1f9690" stroke-width="2.4"/></svg>Sed ut perspiciatis unde omnis iste natus</li>
  <li><svg width="14" height="12" viewBox="0 0 14 12"><path d="M1 6l4 4 8-9" fill="none" stroke="#1f9690" stroke-width="2.4"/></svg>Error sit voluptatem accusanti um dolorem</li>
  <li><svg width="14" height="12" viewBox="0 0 14 12"><path d="M1 6l4 4 8-9" fill="none" stroke="#1f9690" stroke-width="2.4"/></svg>Que laudantium, totam rem aperiam, eaque</li>
  <li><svg width="14" height="12" viewBox="0 0 14 12"><path d="M1 6l4 4 8-9" fill="none" stroke="#1f9690" stroke-width="2.4"/></svg>Ipsa quae ab illo quasi architecto beatae</li>
  <li><svg width="14" height="12" viewBox="0 0 14 12"><path d="M1 6l4 4 8-9" fill="none" stroke="#1f9690" stroke-width="2.4"/></svg>Vitae dicta sunt explicabo</li>
</ul>

<div class="abs video-band"></div>
<div class="abs video-frame" role="img" aria-label="Video still of a visitor adjusting a VR headset under blue club lights"></div>
<svg class="abs play" width="86" height="86" viewBox="0 0 86 86">
  <circle cx="43" cy="43" r="41" fill="rgba(0,0,0,0.15)" stroke="#ffffff" stroke-width="2.5"/>
  <path d="M35 28v30l24-15z" fill="none" stroke="#ffffff" stroke-width="2.5" stroke-linejoin="round"/>
</svg>

<h2 class="abs section-title services-title">OUR SERVICES</h2>
<p class="abs services-sub">Sed ut perspiciatis unde omnis iste natus error sit voluptatem accusantium doloremque laudantium</p>

<div class="abs service" style="left:112px">
  <div class="service-photo" role="img" aria-label="Free roam VR player with headset in warm light" style="background:linear-gradient(160deg,#c98a5a 0%,#6b4a3a 45%,#1e1e1e 100%)"></div>
  <div class="service-label">Free Roam VR Experiences</div>
</div>
<div class="abs service" style="left:358px">
  <div class="service-photo" role="img" aria-label="Woman in VR headset walking on an omnidirectional treadmill" style="background:linear-gradient(160deg,#e6e6e6 0%,#bcbcbc 50%,#3a3a3a 100%)"></div>
  <div class="service-label">Trundla</div>
</div>
<div class="abs service" style="left:606px">
  <div class="service-photo" role="img" aria-label="Visitors seated at stand alone VR stations" style="background:linear-gradient(160deg,#d8cfc4 0%,#a89a88 50%,#5f7a5a 100%)"></div>
  <div class="service-label">Stand Alone VR Stations</div>
</div>
<div class="abs service" style="left:852px">
  <div class="service-photo" role="img" aria-label="Rider in VR headset on a motorbike simulator" style="background:linear-gradient(160deg,#5a6270 0%,#2c2e8c 55%,#14164a 100%)"></div>
  <div class="service-label">VR Simulator Rides</div>
</div>

<footer class="abs footer"></footer>
<div class="abs footer-brand">Orbit Voltix VR</div>
<nav class="abs footer-nav">
  <span>HOME</span><span>|</span><span>ABOUT US</span><span>|</span><span>SERVICES</span><span>|</span><span>NEWS</span><span>|</span><span>CONTACT US</span>
</nav>
<p class="abs copyright">© Copyright-2019 Orbit Voltix VR. All rights reserved.</p>

</body>
</html>
```